Design a large parking banner – mandatory ticket validation in the shop

Banner Size:
548 cm (width) x 154 cm (height)
Note: The banner will be placed in a metal frame at our parking lot entrance, fully visible to every incoming truck driver. The message must be easy to read from a distance.
Goal of the Banner:
To inform all truck drivers that they must validate their entry ticket inside the shop, even if they are parking for a short time.
The message must be displayed in multiple languages for international drivers.
Mandatory Content:
Main message – in multiple languages (clearly separated or stacked):
Dutch (NL): Vergeet je ticket niet te valideren in de shop – verplicht, ook bij kort parkeren!
French (FR): N'oubliez pas de valider votre ticket à la boutique – obligatoire, même pour un court arrêt !
English (EN): Don't forget to validate your entry ticket in the shop – mandatory, even for short stops!
German (DE): Vergessen Sie nicht, Ihr Einfahrticket im Shop zu entwerten – Pflicht, auch bei kurzem Parken!
Polish (PL): Nie zapomnij zatwierdzić biletu w sklepie – obowiązkowe, nawet przy krótkim postoju!
Romanian (RO): Nu uitați să validați biletul în magazin – obligatoriu, chiar și pentru opriri scurte!
You can include more languages if space allows, but these are essential.
Opening Hours Block (in one section below):
Shop Opening Hours
Mon – Fri: 05:30 – 22:00
Sat & Sun: 08:00 – 22:00
Style & Branding:
The design must match the visual identity of Haulport 41Ter
Please refer to the attached photos of existing parking signage for guidance on colors, typography, and layout style
Our logo (attached) must be clearly visible and professionally integrated
Feel free to use icons or pictograms to visually support the message (e.g., ticket, truck, arrow)
Readability is key – large, bold text and high contrast colors that are visible from a distance
Target Audience:
International truck drivers – people who need fast, clear communication. Not everyone speaks the local language, so visual clarity and multilingual messaging are critical.
File Requirements:
Print-ready file (PDF or EPS) – 300 dpi at 1:10 scale
Include 5 cm bleed on all sides
Provide open source files if possible (AI or PSD)

```html
<!DOCTYPE html>
<html lang="en">
<head>
<meta charset="utf-8">
<title>Haulport 41Ter – Ticket Validation Banner</title>
<link href="https://fonts.googleapis.com/css2?family=Bebas+Neue&display=swap" rel="stylesheet">
<style>
  :root {
    --navy: #25265a;
    --red: #e30f1b;
    --blue: #1a7cc4;
    --white: #ffffff;
    --backdrop: #e9ecf1;
  }
  * { margin: 0; padding: 0; box-sizing: border-box; }
  html, body { width: 1200px; height: 1176px; overflow: hidden; }
  body {
    background: var(--backdrop);
    font-family: "Bebas Neue", "Arial Narrow", sans-serif;
    position: relative;
  }
  .banner {
    position: absolute;
    left: 0; top: 420px;
    width: 1200px; height: 337px;
    background: var(--navy);
    overflow: hidden;
  }
  .brand {
    position: absolute;
    left: 52px; top: 62px;
    width: 300px;
  }
  .brand-name {
    display: flex;
    align-items: center;
    gap: 10px;
    color: var(--white);
    font-size: 60px;
    line-height: 0.9;
    letter-spacing: 1px;
  }
  .brand-mark {
    width: 22px; height: 22px;
    background: var(--blue);
    flex: none;
  }
  .brand-rule {
    margin-top: 14px;
    width: 180px; height: 6px;
    background: var(--red);
  }
  .amenities {
    position: absolute;
    left: 56px; top: 212px;
  }
  .messages {
    position: absolute;
    left: 419px; top: 33px;
    list-style: none;
  }
  .message {
    position: relative;
    height: 40.2px;
    padding-left: 18px;
    color: var(--white);
    font-size: 21px;
    line-height: 26px;
    letter-spacing: 0.2px;
    white-space: nowrap;
  }
  .message::before {
    content: "›";
    position: absolute;
    left: 0; top: -1px;
    color: var(--red);
    font-size: 26px;
    font-family: Arial, sans-serif;
    font-weight: bold;
  }
  .message::after {
    content: "";
    position: absolute;
    left: 20px; top: 29px;
    width: 720px; height: 2px;
    background: linear-gradient(90deg, var(--red) 75%, rgba(227,15,27,0));
  }
  .message:last-child::after { display: none; }
  .hours {
    position: absolute;
    left: 0; bottom: 0;
    width: 1200px; height: 56px;
  }
  .hours-shapes { position: absolute; inset: 0; }
  .hours-label, .hours-time {
    position: absolute;
    bottom: 4px;
    color: var(--white);
    line-height: 1;
  }
  .hours-label { left: 46px; font-size: 40px; }
  .hours-time { font-size: 33px; bottom: 6px; }
  .hours-weekdays { left: 465px; }
  .hours-weekend { left: 884px; }
</style>
</head>
<body>
  <section class="banner" aria-label="Ticket validation banner">
    <div class="brand">
      <div class="brand-name"><span>Haulport<br>41Ter</span><span class="brand-mark"></span></div>
      <div class="brand-rule"></div>
    </div>

    <svg class="amenities" width="282" height="40" viewBox="0 0 282 40" fill="#fff" aria-label="Amenities: parking, shop, showers, restaurant, toilets, lounge">
      <!-- parking / truck -->
      <rect x="2" y="12" width="34" height="16"/>
      <rect x="8" y="6" width="22" height="8"/>
      <circle cx="10" cy="32" r="4"/><circle cx="28" cy="32" r="4"/>
      <!-- cart -->
      <path d="M50 6h6l5 18h18l4-12H60" fill="none" stroke="#fff" stroke-width="4" stroke-linejoin="round"/>
      <circle cx="63" cy="32" r="4"/><circle cx="77" cy="32" r="4"/>
      <!-- shower -->
      <path d="M100 38V12q0-8 8-8h6" fill="none" stroke="#fff" stroke-width="4"/>
      <path d="M112 10h12l-4 6h-4z"/>
      <circle cx="116" cy="22" r="1.8"/><circle cx="122" cy="24" r="1.8"/><circle cx="118" cy="29" r="1.8"/><circle cx="125" cy="30" r="1.8"/><circle cx="120" cy="35" r="1.8"/>
      <!-- cutlery -->
      <ellipse cx="145" cy="12" rx="5" ry="9"/><rect x="143" y="18" width="4" height="20"/>
      <rect x="155" y="4" width="3" height="12"/><rect x="160" y="4" width="3" height="12"/><rect x="165" y="4" width="3" height="12"/>
      <rect x="155" y="14" width="13" height="4"/><rect x="159.5" y="16" width="4" height="22"/>
      <rect x="172" y="4" width="5" height="34"/>
      <!-- toilets -->
      <circle cx="192" cy="6" r="4"/><path d="M186 12h12l3 14h-4v12h-10V26h-4z"/>
      <rect x="205" y="2" width="2" height="36"/>
      <circle cx="216" cy="6" r="4"/><rect x="210" y="12" width="12" height="16"/><rect x="211" y="26" width="4" height="12"/><rect x="217" y="26" width="4" height="12"/>
      <!-- lounge -->
      <circle cx="246" cy="8" r="4"/><circle cx="266" cy="8" r="4"/>
      <rect x="240" y="14" width="12" height="10" rx="3"/><rect x="260" y="14" width="12" height="10" rx="3"/>
      <rect x="236" y="24" width="42" height="5"/>
      <circle cx="246" cy="33" r="4"/><circle cx="266" cy="33" r="4"/>
    </svg>

    <ul class="messages">
      <li class="message" lang="nl">Vergeet je ticket niet te valideren in de shop – verplicht, ook bij kort parkeren!</li>
      <li class="message" lang="fr">N'oubliez pas de valider votre ticket à la boutique – obligatoire, même pour un court arrêt !</li>
      <li class="message" lang="en">Don't forget to validate your entry ticket in the shop – mandatory, even for short stops!</li>
      <li class="message" lang="de">Vergessen Sie nicht, Ihr Einfahrticket im Shop zu entwerten – Pflicht, auch bei kurzem Parken!</li>
      <li class="message" lang="pl">Nie zapomnij zatwierdzić biletu w sklepie – obowiązkowe, nawet przy krótkim postoju!</li>
      <li class="message" lang="ro">Nu uitați să validați biletul în magazin – obligatoriu, chiar și pentru opriri scurte!</li>
    </ul>

    <div class="hours">
      <svg class="hours-shapes" width="1200" height="56" viewBox="0 0 1200 56" aria-hidden="true">
        <rect x="0" y="0" width="1200" height="56" fill="var(--blue)"/>
        <rect x="0" y="0" width="1200" height="6" fill="var(--red)"/>
        <polygon points="0,0 420,0 386,56 0,56" fill="var(--red)"/>
        <polygon points="812,6 832,6 804,56 784,56" fill="var(--white)"/>
      </svg>
      <span class="hours-label">Shop Opening Hours</span>
      <span class="hours-time hours-weekdays">Mon – Fri: 05:30 – 22:00</span>
      <span class="hours-time hours-weekend">Sat &amp; Sun: 08:00 – 22:00</span>
    </div>
  </section>
</body>
</html>
```